Business Card Design - ChoiceCraft

Looking for creative, modern design, two sided for ChoiceCraft that is consistent with color and feel of website www.choicecraftpro.net.
Updates

Back of card will be used to promote products or have a quote revolving around decisions, change, leadership, innovation, creativity. Back should also have space to promote website, but optional to use the icon. Front of the card will need to use the icon and have standard place for name, job title, phone and email. We are not looking to put a mailing address or fax. Also want space to place a few words/phrase explaining what we do...such as individual growth and organizational development or tools, training, information...in addition, want the facebook icon small on the front somewhere as we are also on facebook.

Vector file uploaded of icon.

Target Market(s)

Professional coaching for individual growth and organizational development

Industry/Entity Type

Business

Requirements
Must have
• Icon...see attached.

```html
<!DOCTYPE html>
<html lang="en">
<head>
<meta charset="utf-8">
<title>ChoiceCraft Business Card</title>
<link rel="stylesheet" href="https://fonts.googleapis.com/css2?family=PT+Sans:wght@400;700&family=Arimo:wght@400;700&display=swap">
<style>
  :root {
    --stage: #d9dbde;
    --card: #ffffff;
    --card-edge: #3a3d42;
    --ink: #2b2b2b;
    --ink-soft: #555a60;
    --accent: #2a9ad6;
    --brand-blue: #5fa8e0;
    --sky-light: #e7f0fb;
    --sky-mid: #c3d6ee;
    --head-edge: #8d95b8;
  }
  * { box-sizing: border-box; margin: 0; padding: 0; }
  html, body { width: 1200px; height: 1043px; overflow: hidden; }
  body {
    background: var(--stage);
    position: relative;
    font-family: "PT Sans", sans-serif;
    color: var(--ink);
  }
  .card {
    position: absolute;
    background: var(--card);
    border: 2px solid var(--card-edge);
    border-radius: 30px;
    overflow: hidden;
  }
  .card-front { left: 67px; top: 63px; width: 784px; height: 448px; }
  .card-back { left: 350px; top: 554px; width: 820px; height: 442px; font-family: "Arimo", sans-serif; }

  .brand-mark {
    position: absolute; left: 74px; top: 22px;
    width: 146px; height: 146px; border-radius: 50%;
    background: radial-gradient(circle at 40% 35%, var(--sky-light), var(--brand-blue));
  }
  .brand-name {
    position: absolute; left: 43px; top: 198px;
    font-size: 26px; font-weight: 700; letter-spacing: 0.2px;
  }
  .contact-list { position: absolute; left: 43px; top: 255px; list-style: none; }
  .contact-list li {
    display: flex; align-items: center; gap: 9px;
    font-size: 19px; line-height: 27px; color: var(--ink);
  }
  .contact-list svg { width: 14px; height: 14px; flex: none; }
  .social-square { width: 12px; height: 12px; background: #3b5aa0; border-radius: 2px; margin: 0 1px; }
  .tagline {
    position: absolute; left: 43px; top: 372px;
    font-size: 19px; line-height: 24px; color: var(--ink);
  }
  .head-art {
    position: absolute; left: 426px; top: 27px; width: 410px; height: 450px;
    background: linear-gradient(180deg, var(--sky-mid) 0%, var(--sky-light) 55%, #d2e1f4 100%);
    border: 3px solid var(--head-edge);
    border-radius: 48% 46% 8% 30% / 40% 38% 8% 20%;
  }
  .person { position: absolute; left: 500px; top: 270px; width: 160px; text-align: center; }
  .person-name { font-size: 28px; font-weight: 700; color: var(--ink-soft); }
  .person-title { font-size: 21px; color: var(--ink-soft); margin-top: 2px; }

  .quote-list { position: absolute; left: 52px; top: 30px; list-style: none; }
  .quote { position: relative; padding-left: 26px; margin-bottom: 24px; }
  .quote::before {
    content: "\201C"; position: absolute; left: 0; top: -10px;
    font-size: 38px; font-weight: 700; color: var(--ink-soft); font-family: Georgia, serif;
  }
  .quote-text { font-size: 20px; color: var(--ink-soft); }
  .quote-text::after {
    content: "\201D"; font-size: 38px; font-weight: 700; color: var(--ink-soft);
    font-family: Georgia, serif; vertical-align: -18px; line-height: 0; margin-left: 2px;
  }
  .quote-author { font-size: 20px; font-weight: 700; color: var(--accent); margin-top: 4px; }
  .quote-author span { color: var(--ink-soft); font-weight: 400; }
  .back-mark {
    position: absolute; left: 540px; top: 270px;
    width: 132px; height: 132px; border-radius: 50%;
    background: radial-gradient(circle at 40% 35%, var(--sky-light), var(--brand-blue));
  }
</style>
</head>
<body>
  <section class="card card-front">
    <div class="brand-mark"></div>
    <div class="brand-name">ChoiceCraft</div>
    <ul class="contact-list">
      <li><svg viewBox="0 0 14 14"><path d="M3 1l3 3-1.5 1.5a8 8 0 0 0 4 4L10 8l3 3-2 2C6 13 1 8 1 3z" fill="none" stroke="#333" stroke-width="1.3"/></svg>555-014-2279</li>
      <li><svg viewBox="0 0 14 14"><rect x="1" y="3" width="12" height="9" fill="none" stroke="#333" stroke-width="1.3"/><path d="M1 3l6 5 6-5" fill="none" stroke="#333" stroke-width="1.3"/></svg>hello@choicecraftpro.net</li>
      <li><svg viewBox="0 0 14 14"><circle cx="7" cy="7" r="6" fill="none" stroke="#333" stroke-width="1.3"/><path d="M1 7h12M7 1c-3 3-3 9 0 12M7 1c3 3 3 9 0 12" fill="none" stroke="#333" stroke-width="1"/></svg>www.choicecraftpro.net</li>
      <li><span class="social-square"></span>/choicecraftpro</li>
    </ul>
    <p class="tagline">Supporting individual growth<br>and organizational development.</p>
    <div class="head-art" role="img" aria-label="Illustration of a head profile in soft blue with silver gears inside"></div>
    <div class="person">
      <div class="person-name">Your Name</div>
      <div class="person-title">Title</div>
    </div>
  </section>

  <section class="card card-back">
    <ul class="quote-list">
      <li class="quote"><div class="quote-text">Try not to become a man of success, but rather a man of value.</div><div class="quote-author"><span>- </span>Mara Ellison</div></li>
      <li class="quote"><div class="quote-text">The only constant is change.</div><div class="quote-author"><span>- </span>Theo Varga</div></li>
      <li class="quote"><div class="quote-text">We are what we repeatedly do. Excellence is not an act, it is a habit.</div><div class="quote-author"><span>- </span>Ilan Petros</div></li>
      <li class="quote"><div class="quote-text">Simplicity is the ultimate sophistication.</div><div class="quote-author"><span>- </span>Lucia Renn</div></li>
      <li class="quote"><div class="quote-text">Life is not fair - get used to it.</div><div class="quote-author"><span>- </span>Owen Hartley</div></li>
    </ul>
    <div class="back-mark"></div>
  </section>
</body>
</html>
```